i need a business card design for my family investment company "quorin investments" based in qasrah. its a diverse investment firm focusing on education, hospitality and automotive. the design has to be modern and try to incorporate the logo "E" in the design. details on card as follow

Yusuf K Bin Tarrah
Managing Director
yusuf@quorin-mail.ae
www.quorin-mail.ae

Harbor district,palwick tower, office 1408, qasrah
tel. 04 3850927
mobile.050 9184203

card used for networking events and investor meetings

Hospitality

```html
<!DOCTYPE html>
<html lang="en">
<head>
<meta charset="utf-8">
<title>Quorin Investments – Business Card</title>
<link rel="stylesheet" href="https://fonts.googleapis.com/css2?family=Lato:wght@300;400;700&display=swap">
<style>
  :root {
    --backdrop: #3b3b3d;
    --card-white: #ffffff;
    --card-black: #050505;
    --brand-blue: #4a76a0;
    --ink: #161616;
    --divider: #9a9a9a;
    --white: #ffffff;
  }
  * { margin: 0; padding: 0; box-sizing: border-box; }
  html, body {
    width: 1200px; height: 926px; overflow: hidden;
    background: var(--backdrop);
    font-family: "Lato", sans-serif;
  }
  .sheet {
    width: 1200px; height: 926px;
    display: flex; flex-direction: column;
    align-items: center; justify-content: center; gap: 40px;
  }
  .card {
    width: 700px; height: 400px;
    position: relative; overflow: hidden;
    box-shadow: 0 10px 30px rgba(0,0,0,.35);
  }

  /* Front */
  .card--front { background: var(--card-white); }
  .wordmark {
    font-weight: 300; text-transform: uppercase; text-align: center;
    line-height: 1; white-space: nowrap;
  }
  .card--front .wordmark {
    position: absolute; top: 48px; left: 0; right: 0;
    color: var(--ink); font-size: 30px; letter-spacing: 10px;
  }
  .holder {
    position: absolute; top: 118px; left: 0; right: 0; text-align: center;
  }
  .holder__name {
    color: var(--brand-blue); font-size: 30px; font-weight: 400;
  }
  .holder__name strong { font-weight: 700; }
  .holder__role {
    color: var(--ink); font-size: 19px; letter-spacing: 1.5px; margin-top: 2px;
  }
  .contacts {
    position: absolute; top: 222px; left: 0; right: 0;
    display: flex; justify-content: center; align-items: stretch;
    font-size: 19px; color: var(--ink);
  }
  .contacts__col { display: flex; flex-direction: column; gap: 8px; padding: 0 18px; white-space: nowrap; }
  .contacts__col--left { text-align: right; }
  .contacts__divider { width: 1px; background: var(--divider); margin: 4px 0; }
  .label { color: var(--brand-blue); font-weight: 700; }
  .address-band {
    position: absolute; left: 0; right: 0; bottom: 0; height: 74px;
    background: var(--brand-blue); color: var(--white);
    display: flex; align-items: center; justify-content: center;
    font-size: 21px; font-weight: 400; letter-spacing: 1.5px; text-transform: uppercase;
    white-space: nowrap;
  }

  /* Back */
  .card--back {
    background: var(--card-black);
    display: flex; align-items: center; justify-content: center;
  }
  .card--back .wordmark {
    color: var(--white); font-size: 38px; letter-spacing: 10px;
  }
</style>
</head>
<body>
<main class="sheet">
  <section class="card card--front" aria-label="Card front">
    <div class="wordmark">Quorin Investments</div>
    <div class="holder">
      <h1 class="holder__name">Yusuf <strong>K Bin Tarrah</strong></h1>
      <p class="holder__role">managing director</p>
    </div>
    <div class="contacts">
      <div class="contacts__col contacts__col--left">
        <span><span class="label">tel.</span> 04 3850927</span>
        <span><span class="label">web.</span> www.quorin-mail.ae</span>
      </div>
      <div class="contacts__divider"></div>
      <div class="contacts__col">
        <span><span class="label">mobile.</span> 050 9184203</span>
        <span><span class="label">email.</span> yusuf@quorin-mail.ae</span>
      </div>
    </div>
    <div class="address-band">Harbor District, Palwick Tower, Office 1408, Qasrah</div>
  </section>

  <section class="card card--back" aria-label="Card back">
    <div class="wordmark">Quorin Investments</div>
  </section>
</main>
</body>
</html>
```